New LLC consulting company needs a business card design

I need a business card design for new company in Alexandria Virginia called TK Verdane Consulting LLC. The company is focused on consulting for defense and national security issues with expertise in nuclear and space topics. I would like to see designs that are simple and I am open to colors except for brown.

Target Market(s)

All businesses that are seeking consulting help

Industry/Entity Type

Consulting

Contact Information for Business Card

Name of company - TK Verdane Consulting LLC; name (Delia Pratt) President; email: prattdq47@mailvessa.com; Phone: 703-555-0142

Requirements
Must have
• The details described above
Nice to have
• I'm open to all ideas
Should not have
• No brown

```html
<!DOCTYPE html>
<html lang="en">
<head>
<meta charset="utf-8">
<title>TK Verdane Consulting LLC – Business Card</title>
<link rel="stylesheet" href="https://fonts.googleapis.com/css2?family=Poppins:wght@400;500;600;700&display=swap">
<style>
  :root {
    --backdrop: #f0f0f0;
    --card: #ffffff;
    --blue: #1075bf;
    --charcoal: #38393b;
    --ink: #111111;
    --shadow: rgba(0, 0, 0, 0.28);
  }
  * { box-sizing: border-box; margin: 0; padding: 0; }
  html, body {
    width: 1200px; height: 987px; overflow: hidden;
    background: var(--backdrop);
    font-family: "Poppins", sans-serif;
  }
  .canvas { position: relative; width: 1200px; height: 987px; }
  .card {
    position: absolute; left: 245px; width: 710px; height: 406px;
    background: var(--card); border-radius: 31px; overflow: hidden;
    box-shadow: 0 14px 30px var(--shadow);
  }
  .card--front { top: 68px; }
  .card--back { top: 515px; }
  .card__band { position: absolute; left: 0; bottom: 0; width: 710px; height: 26px; display: block; }
  .band-blue { fill: var(--blue); }
  .band-dark { fill: var(--charcoal); }

  .wordmark {
    position: absolute; display: flex; align-items: center;
    color: var(--charcoal); font-weight: 600; white-space: nowrap;
  }
  .wordmark__dot { flex: none; border-radius: 50%; background: var(--blue); }
  .card--front .wordmark {
    left: 0; right: 0; top: 160px; justify-content: center; gap: 14px;
    font-size: 32px; letter-spacing: 0.5px;
  }
  .card--front .wordmark__dot { width: 22px; height: 22px; }
  .card--back .wordmark {
    left: 30px; top: 176px; gap: 12px; font-size: 22px; line-height: 1.2;
  }
  .card--back .wordmark__dot { width: 18px; height: 18px; }

  .divider {
    position: absolute; left: 355px; top: 98px; width: 1px; height: 206px;
    background: var(--charcoal);
  }
  .contact { position: absolute; left: 417px; top: 132px; }
  .contact__name { color: var(--blue); font-size: 34px; line-height: 1; font-weight: 400; }
  .contact__name strong { font-weight: 600; }
  .contact__title { margin-top: 6px; font-size: 17px; font-weight: 500; color: var(--ink); }
  .contact__list { list-style: none; margin-top: 26px; }
  .contact__item {
    display: flex; align-items: center; gap: 10px;
    font-size: 18px; color: var(--ink); line-height: 24px;
  }
  .contact__item + .contact__item { margin-top: 0; }
  .contact__icon { width: 16px; height: 16px; flex: none; }
</style>
</head>
<body>
<main class="canvas">
  <section class="card card--front">
    <div class="wordmark">
      <span class="wordmark__dot"></span>
      <span class="wordmark__name">TK Verdane Consulting LLC</span>
    </div>
    <svg class="card__band" viewBox="0 0 710 26" preserveAspectRatio="none" aria-hidden="true">
      <polygon class="band-blue" points="0,0 316,0 354,26 0,26"/>
      <polygon class="band-dark" points="343,0 710,0 710,26 381,26"/>
    </svg>
  </section>

  <section class="card card--back">
    <div class="wordmark">
      <span class="wordmark__dot"></span>
      <span class="wordmark__name">TK Verdane<br>Consulting LLC</span>
    </div>
    <div class="divider"></div>
    <div class="contact">
      <h1 class="contact__name"><strong>Delia</strong> Pratt</h1>
      <p class="contact__title">President</p>
      <ul class="contact__list">
        <li class="contact__item">
          <svg class="contact__icon" viewBox="0 0 24 24" aria-hidden="true">
            <path fill="var(--blue)" d="M6.6 10.8a15.1 15.1 0 0 0 6.6 6.6l2.2-2.2c.3-.3.7-.4 1-.2 1.1.4 2.3.6 3.6.6.6 0 1 .4 1 1V20c0 .6-.4 1-1 1A17 17 0 0 1 3 4c0-.6.4-1 1-1h3.5c.6 0 1 .4 1 1 0 1.3.2 2.5.6 3.6.1.3 0 .7-.2 1z"/>
            <path fill="none" stroke="var(--blue)" stroke-width="1.8" stroke-linecap="round" d="M14 3.5a7 7 0 0 1 6.5 6.5M14 7a3.5 3.5 0 0 1 3 3"/>
          </svg>
          <span>703-555-0142</span>
        </li>
        <li class="contact__item">
          <svg class="contact__icon" viewBox="0 0 24 24" aria-hidden="true">
            <path fill="var(--blue)" d="M2 9l10-7 10 7v12H2z"/>
            <path fill="none" stroke="#fff" stroke-width="1.5" d="M2 9l10 7 10-7M2 21l7.5-7M22 21l-7.5-7"/>
            <circle cx="12" cy="8.5" r="2.2" fill="none" stroke="#fff" stroke-width="1.2"/>
          </svg>
          <span>prattdq47@mailvessa.com</span>
        </li>
      </ul>
    </div>
    <svg class="card__band" viewBox="0 0 710 26" preserveAspectRatio="none" aria-hidden="true">
      <polygon class="band-blue" points="0,0 316,0 354,26 0,26"/>
      <polygon class="band-dark" points="343,0 710,0 710,26 381,26"/>
    </svg>
  </section>
</main>
</body>
</html>
```